Boutique custom software development company needs new business card

Our nearly 20 year old custom software development company would like to better include the fact that we are now providing Bitcoin services. These new services are B2B include education (how to acquire and securely hold Bitcoin) and integrating Bitcoin payments into existing ecommerce sites or other existing systems. Please keep the card clean and simple. Attached is our current design and some other files. vextorial.com

Target Market(s)

businesses owners interested in long term relationship

Industry/Entity Type

Custom software development and Bitcoin

Contact Information for Business Card

Dale Parker, dale@vextorial.com, vextorial.com, (888) 555-VXTRL

Font styles to use
Other font styles liked:
• monospace

Requirements
Must have
• double-sided
Nice to have
• clean and simple
Should not have
• physical address

```html
<!DOCTYPE html>
<html lang="en">
<head>
<meta charset="utf-8">
<title>Vextorial business card</title>
<link href="https://fonts.googleapis.com/css2?family=Lato:wght@400;700;900&display=swap" rel="stylesheet">
<style>
  :root {
    --backdrop: #3b3b3b;
    --card: #121212;
    --card-deep: #0b0b0b;
    --blue: #3f74c9;
    --orange: #f07a1c;
    --white: #f2f2f2;
  }
  * { margin: 0; padding: 0; box-sizing: border-box; }
  html, body { width: 1200px; height: 801px; overflow: hidden; }
  body {
    background: var(--backdrop);
    font-family: "Lato", Arial, sans-serif;
    position: relative;
  }
  .card {
    position: absolute;
    top: 252px;
    width: 520px;
    height: 297px;
    background: var(--card);
    border-bottom: 2px solid var(--blue);
    overflow: hidden;
  }
  .card--front { left: 50px; }
  .card--back { left: 630px; }

  .brand {
    position: absolute;
    display: flex;
    align-items: center;
    gap: 8px;
  }
  .brand__mark { width: 14px; height: 14px; background: var(--orange); }
  .brand__name {
    font-weight: 900;
    font-size: 34px;
    letter-spacing: 0.5px;
    color: var(--blue);
    line-height: 1;
  }
  .brand__tagline {
    position: absolute;
    font-size: 12px;
    color: var(--blue);
    letter-spacing: 0.2px;
  }
  .card--front .brand { top: 34px; right: 36px; }
  .card--front .brand__tagline { top: 74px; right: 36px; }

  .holder {
    position: absolute;
    left: 32px;
    top: 170px;
    font-weight: 900;
    font-size: 19px;
    letter-spacing: 0.8px;
    color: var(--blue);
    text-transform: uppercase;
  }
  .divider {
    position: absolute;
    left: 32px;
    right: 36px;
    top: 202px;
    height: 1px;
    background: var(--blue);
  }
  .contacts {
    position: absolute;
    left: 32px;
    top: 218px;
    list-style: none;
  }
  .contacts li {
    display: flex;
    align-items: center;
    gap: 9px;
    font-size: 14px;
    color: var(--white);
    line-height: 24px;
  }
  .contacts svg { width: 12px; height: 12px; fill: var(--orange); }
  .website {
    position: absolute;
    right: 26px;
    bottom: 28px;
    font-size: 14px;
    color: var(--white);
  }
  .website em { font-style: normal; color: var(--orange); }
  .accent-bar {
    position: absolute;
    right: 0;
    bottom: 0;
    width: 160px;
    height: 12px;
    background: var(--orange);
  }

  .pattern-field {
    position: absolute;
    inset: 0;
    background: linear-gradient(135deg, var(--card-deep) 0%, #1d1d1d 45%, var(--card-deep) 100%);
  }
  .card--back .brand { top: 150px; right: 36px; }
  .card--back .brand__tagline { top: 190px; right: 36px; }
</style>
</head>
<body>
  <section class="card card--front" aria-label="Business card front">
    <div class="brand">
      <span class="brand__mark"></span>
      <span class="brand__name">VEXTORIAL</span>
    </div>
    <p class="brand__tagline">developer of custom applications</p>

    <h1 class="holder">Dale Parker</h1>
    <div class="divider"></div>
    <ul class="contacts">
      <li>
        <svg viewBox="0 0 24 24" aria-hidden="true"><path d="M6.6 10.8a15.1 15.1 0 0 0 6.6 6.6l2.2-2.2a1 1 0 0 1 1-.25 11.4 11.4 0 0 0 3.6.57 1 1 0 0 1 1 1V20a1 1 0 0 1-1 1A17 17 0 0 1 3 4a1 1 0 0 1 1-1h3.5a1 1 0 0 1 1 1c0 1.25.2 2.45.57 3.6a1 1 0 0 1-.25 1z"/></svg>
        (888) 555-VXTRL
      </li>
      <li>
        <svg viewBox="0 0 24 24" aria-hidden="true"><path d="M2 5h20v14H2z M2 5l10 8 10-8" fill="var(--orange)"/><path d="M2 5l10 8 10-8" fill="none" stroke="#121212" stroke-width="2"/></svg>
        dale@vextorial.com
      </li>
    </ul>
    <p class="website">www.<em>vextorial</em>.com</p>
    <div class="accent-bar"></div>
  </section>

  <section class="card card--back" aria-label="Business card back">
    <div class="pattern-field" role="img" aria-label="Tiled pattern of the brand symbol in gloss black on matte black"></div>
    <div class="brand">
      <span class="brand__mark"></span>
      <span class="brand__name">VEXTORIAL</span>
    </div>
    <p class="brand__tagline">developer of custom applications</p>
  </section>
</body>
</html>
```